Stationery Design + Business Cards

Stationary (letterhead as A4 210x297mm and Letter 8.5"x11", preferably both master page + 2nd pages)

Also need business cards, standard size 50x88mm, can be vertical or horizontal.

You can use a front/back design for the business cards, or front only.

Looking at the uploaded file (devank, you already have that), I want it to use the first logo on the list (4 colors).

Alternative, try the grayscale version (second file).

I need the following information on the business card (in no particular order, let me know what you come up with): 

Firstname Lastlame 
Title 

Mobile +1 555-204-7391 

VelaMorn, Inc. 
24851 Birchwood Ridge Passage 
Larkvale, OH 46099 
Tel. +1 555-368-4172 
Fax +1 555-619-0834 

Web: www.velamorn.example 
Twitter: twitter/VelaMorn or @VelaMorn 
Facebook: facebook.com/VelaMorn 

For letterhead, just the company name, address + phone number & fax number 

If you think the phone/fax or something else should not be on the business cards, or something could be missing, let me know.

```html
<!DOCTYPE html>
<html lang="en">
<head>
<meta charset="utf-8">
<title>VelaMorn Letterhead</title>
<link href="https://fonts.googleapis.com/css2?family=Source+Sans+3:wght@400&display=swap" rel="stylesheet">
<style>
  :root {
    --canvas: #ffffff;
    --paper: #ffffff;
    --paper-edge: #d6d6d6;
    --paper-shadow: rgba(0, 0, 0, 0.28);
    --brand-blue: #1d4f9e;
    --brand-orange: #ef7d22;
    --band-grey: #6b6b6b;
    --band-text: #ffffff;
  }
  * { box-sizing: border-box; margin: 0; padding: 0; }
  html, body {
    width: 1200px;
    height: 960px;
    overflow: hidden;
    background: var(--canvas);
    font-family: "Source Sans 3", "Myriad Pro", Arial, sans-serif;
  }
  .letterhead {
    position: absolute;
    left: 278px;
    top: 49px;
    width: 663px;
    height: 859px;
    background: var(--paper);
    border: 1px solid var(--paper-edge);
    box-shadow: 0 1px 4px var(--paper-shadow);
  }
  .brand {
    position: absolute;
    display: flex;
    align-items: center;
    gap: 6px;
    color: var(--brand-blue);
    font-weight: 400;
    white-space: nowrap;
  }
  .brand-dot {
    flex: none;
    border-radius: 50%;
    background: var(--brand-orange);
  }
  .brand--header {
    left: 247px;
    top: 49px;
    font-size: 30px;
    letter-spacing: -0.2px;
  }
  .brand--header .brand-dot { width: 22px; height: 22px; }
  .footer-band {
    position: absolute;
    left: 52px;
    top: 801px;
    width: 490px;
    height: 31px;
    background: var(--band-grey);
    color: var(--band-text);
    font-size: 8.8px;
    line-height: 31px;
    padding: 1px 0 0 9px;
    white-space: nowrap;
  }
  .brand--footer {
    left: 528px;
    top: 806px;
    height: 27px;
    padding: 0 4px;
    background: var(--paper);
    border-radius: 14px 0 0 14px;
    font-size: 15px;
  }
  .brand--footer .brand-dot { width: 12px; height: 12px; }
</style>
</head>
<body>
  <main class="letterhead">
    <header class="brand brand--header">
      <span class="brand-dot"></span>
      <span class="brand-name">VelaMorn</span>
    </header>

    <footer>
      <p class="footer-band">VelaMorn, Inc. &nbsp;|&nbsp; 24851 Birchwood Ridge Passage &nbsp;|&nbsp; Larkvale, OH 46099 &nbsp;|&nbsp; Tel. +1 555-368-4172 &nbsp;|&nbsp; Fax +1 555-619-0834</p>
      <div class="brand brand--footer">
        <span class="brand-dot"></span>
        <span class="brand-name">VelaMorn</span>
      </div>
    </footer>
  </main>
</body>
</html>
```